Business Card Design

We are a commercial real estate brokerage in San Francisco, leasing office buildings downtown.
I would like a clean, elegant look. Simple but powerful .

Industry/Entity Type

Business

Contact Information for Business Card

Derek Holloway
lic# 07258143
415.555.0172
derek@velt-commercial.example
velt-commercial.example

```html
<!DOCTYPE html>
<html lang="en">
<head>
<meta charset="utf-8">
<title>Velt Commercial – Business Card</title>
<link rel="stylesheet" href="https://fonts.googleapis.com/css2?family=Source+Sans+3:wght@400;600;700&display=swap">
<style>
  :root {
    --backdrop: #e9e7e4;
    --card: #ffffff;
    --slate-blue: #7488a5;
    --charcoal: #555555;
    --stripe: #5f5f5f;
    --ink-light: #ffffff;
  }
  * { box-sizing: border-box; margin: 0; padding: 0; }
  html, body { width: 1200px; height: 900px; overflow: hidden; }
  body {
    position: relative;
    background: var(--backdrop);
    font-family: "Source Sans 3", "Myriad Pro", Arial, sans-serif;
  }
  .card {
    position: absolute;
    background: var(--card);
    border-radius: 18px;
    overflow: hidden;
    box-shadow: 0 6px 18px rgba(0,0,0,0.12);
  }
  .card--front { left: 78px; top: 35px; width: 588px; height: 362px; }
  .card--back  { left: 390px; top: 507px; width: 564px; height: 348px; }

  .card__diagonal { position: absolute; inset: 0; width: 100%; height: 100%; }

  .wordmark {
    position: absolute;
    color: var(--charcoal);
    font-weight: 700;
    text-transform: uppercase;
    line-height: 0.95;
  }
  .card--front .wordmark { left: 48px; top: 60px; font-size: 44px; }
  .card--front .wordmark span { display: block; font-size: 27px; letter-spacing: 1px; }

  .contact {
    position: absolute;
    right: 36px;
    top: 173px;
    text-align: right;
    color: var(--ink-light);
  }
  .contact__name { font-size: 22px; font-weight: 600; margin-bottom: 16px; }
  .contact__licence { font-size: 15px; font-weight: 600; margin-bottom: 24px; }
  .contact__line {
    display: flex; justify-content: flex-end; align-items: center; gap: 8px;
    font-size: 15px; line-height: 25px;
  }
  .contact__icon { width: 11px; height: 11px; flex: none; }

  .brand-lockup {
    position: absolute; left: 110px; top: 130px;
    display: flex; align-items: center; gap: 22px;
  }
  .brand-lockup__square { width: 64px; height: 64px; background: var(--slate-blue); }
  .card--back .wordmark { position: static; color: var(--slate-blue); font-size: 50px; }
  .card--back .wordmark span { display: block; font-size: 27px; letter-spacing: 0.5px; }
</style>
</head>
<body>
  <section class="card card--front" aria-label="Card front">
    <svg class="card__diagonal" viewBox="0 0 588 362" preserveAspectRatio="none" aria-hidden="true">
      <polygon points="588,0 588,362 0,362" fill="var(--slate-blue)"/>
      <polygon points="574,0 588,0 588,6 8,362 0,362 0,356" fill="var(--stripe)"/>
    </svg>
    <div class="wordmark">Velt<span>Commercial</span></div>
    <div class="contact">
      <p class="contact__name">Derek Holloway</p>
      <p class="contact__licence">Lic# 07258143</p>
      <p class="contact__line">415.555.0172
        <svg class="contact__icon" viewBox="0 0 12 12" aria-hidden="true"><path d="M2.5 0.8l2 2.2-1 1.4c.7 1.6 2 2.9 3.6 3.6l1.4-1 2.2 2-1.3 1.9C5 10.6 1.4 7 .6 2.1z" fill="#fff"/></svg>
      </p>
      <p class="contact__line">derek@velt-commercial.example
        <svg class="contact__icon" viewBox="0 0 12 12" aria-hidden="true"><rect x="0.5" y="2.5" width="11" height="7.5" fill="#fff"/><path d="M0.5 2.5l5.5 4 5.5-4" stroke="var(--slate-blue)" fill="none"/></svg>
      </p>
      <p class="contact__line">velt-commercial.example
        <svg class="contact__icon" viewBox="0 0 12 12" aria-hidden="true"><path d="M5 7l2-2M4.5 5.5l-2 2a1.6 1.6 0 002 2l2-2M7.5 6.5l2-2a1.6 1.6 0 00-2-2l-2 2" stroke="#fff" stroke-width="1.3" fill="none" stroke-linecap="round"/></svg>
      </p>
    </div>
  </section>

  <section class="card card--back" aria-label="Card back">
    <div class="brand-lockup">
      <div class="brand-lockup__square"></div>
      <div class="wordmark">Velt<span>Commercial</span></div>
    </div>
  </section>
</body>
</html>
```